Billboard Velto-Link Systems

Design of an A0 billboard (landscape, will be printed on adhesive foil) of our company with reference to the website (www.velto-link.example) and the activity through keywords / phrases such as Fastest data radio you can buy, data radio safe and independent , ...
Explanation: we set up radio networks for long-range data transmission, which work on our own frequencies and are therefore independent of the provider. The systems are used for water and energy supply systems, sewage systems, environmental measurement networks, ...

Industry/Entity Type

Water-, Energie- Distribution, Abwasser...

Requirements
Must have
• Logo, link on website
Nice to have
• Message
Should not have
• picture of our old product from present web. I will be discontinued shortly. Please use the new one I uploaded here.

```html
<!DOCTYPE html>
<html lang="en">
<head>
<meta charset="utf-8">
<title>Velto-Link Systems Billboard</title>
<link href="https://fonts.googleapis.com/css2?family=Figtree:wght@700&family=Fira+Sans+Condensed:wght@300&display=swap" rel="stylesheet">
<style>
  :root {
    --brand-blue: #5a88a0;
    --ink-grey: #474747;
    --paper: #ffffff;
    --photo-light: #b9b2a8;
    --photo-dark: #6e675f;
  }
  * { margin: 0; padding: 0; box-sizing: border-box; }
  html, body { width: 1200px; height: 848px; overflow: hidden; background: var(--paper); }
  .billboard { position: relative; width: 1200px; height: 848px; background: var(--paper); overflow: hidden; }
  .backdrop { position: absolute; inset: 0; width: 1200px; height: 848px; }
  .brand-name {
    position: absolute; left: 71px; top: 88px;
    font-family: "Figtree", sans-serif; font-weight: 700;
    font-size: 38px; letter-spacing: 0.5px; color: var(--paper);
  }
  .headline {
    position: absolute; left: 72px; top: 318px;
    font-family: "Figtree", sans-serif; font-weight: 700;
    font-size: 101px; line-height: 120px; color: var(--brand-blue);
    letter-spacing: -0.5px;
  }
  .tagline {
    position: absolute; left: 72px; top: 580px;
    font-family: "Fira Sans Condensed", sans-serif; font-weight: 300;
    font-size: 46px; color: var(--ink-grey); letter-spacing: 0.5px;
  }
  .web-link {
    position: absolute; left: 71px; top: 694px; width: 533px; height: 85px;
    border: 2px solid var(--brand-blue); border-radius: 22px;
    display: flex; align-items: center; justify-content: center;
    font-family: "Fira Sans Condensed", sans-serif; font-weight: 300;
    font-size: 49px; color: var(--brand-blue);
  }
</style>
</head>
<body>
  <main class="billboard">
    <svg class="backdrop" viewBox="0 0 1200 848" aria-hidden="false">
      <defs>
        <linearGradient id="photoTone" x1="0" y1="0" x2="1" y2="1">
          <stop offset="0" stop-color="var(--photo-light)"/>
          <stop offset="0.6" stop-color="var(--photo-dark)"/>
          <stop offset="1" stop-color="var(--photo-light)"/>
        </linearGradient>
      </defs>
      <path class="site-photo" role="img" aria-label="Aerial view of circular basins at a water treatment plant"
            d="M340,0 H1200 V800 C1060,500 850,230 543,102 C470,72 400,38 340,0 Z"
            fill="url(#photoTone)"/>
      <path class="corner-band"
            d="M0,0 H1045 C860,20 700,55 543,102 C330,165 150,245 0,335 Z"
            fill="var(--brand-blue)" opacity="0.92"/>
    </svg>

    <div class="brand-name">Velto-Link Systems</div>

    <h1 class="headline">Buy a Reliable<br>Data Radio</h1>

    <p class="tagline">SAFE | FAST | INDEPENDENT</p>

    <div class="web-link">www.velto-link.example</div>
  </main>
</body>
</html>
```